Web Design Project for a beach town business owner who supports new families with their babies.

I'm looking for a basic website with the following pages: home, about, services, FAQs, blog, and contact page. I have images and content ready to go.

Target Market(s)

Men and women between the ages of 22 and 42, growing families

Industry/Entity Type

Postpartum Doula

Coding

Number of Pages Required

Font styles to use
Serif
Other font styles liked:
• My logo font is "Nexa Bold" - so coordinating fonts with that are ideal

Colors
00AB8E
00BBA5
67D7C9
C6EFE9
E9F9F6
EE7325
F08F49
F5BC92
FAE3D3
FDF4ED

Requirements
Must have
• Warm and professional vibe, multicultural images, aligned with my branding colors and font ("Nexa Bold"; COLORS: light blue hex: #2FCEC2 R: 47 G: 206 B: 194 dark blue hex: #007C7C R: 0 G: 124 B: 124 orange hex: #F77B4E R: 247 G: 123 B: 78), good SEO
Should not have
• Ultra feminine images, baby bottles, cutesy images.

```html
<!DOCTYPE html>
<html lang="en">
<head>
<meta charset="utf-8">
<title>Harbor Nest Postpartum Care</title>
<link rel="stylesheet" href="https://fonts.googleapis.com/css2?family=Montserrat:wght@500;600;700&family=Lato:wght@400;700&display=swap">
<style>
:root{
  --teal-light:#2fcec2;
  --teal-dark:#0f6e6e;
  --teal-band:#127272;
  --orange:#f7653a;
  --ink:#2a2a2a;
  --footer:#242424;
  --white:#ffffff;
}
*{box-sizing:border-box;margin:0;padding:0}
html,body{width:1200px;height:3199px;overflow:hidden}
body{position:relative;background:var(--white);font-family:"Lato",sans-serif;color:var(--ink)}
.abs{position:absolute}
.hero{left:0;top:0;width:1200px;height:738px;background:radial-gradient(ellipse at 45% 55%,#8a8a8a 0%,#4a4a4a 45%,#1c1c1c 100%)}
.brand{left:75px;top:74px;display:flex;align-items:center;gap:14px}
.brand-dot{width:56px;height:56px;border-radius:50%;background:var(--white)}
.brand-name{font-family:"Montserrat",sans-serif;font-weight:700;font-size:22px;color:var(--white)}
.nav{top:78px;left:0;width:1200px;height:49px}
.nav a{position:absolute;top:0;height:49px;line-height:49px;transform:translateX(-50%);font-family:"Montserrat",sans-serif;font-weight:700;font-size:16px;color:var(--white);text-decoration:none;letter-spacing:.3px}
.nav a.active{background:var(--teal-light);border-radius:25px;width:118px;text-align:center}
.hero-title{top:322px;left:0;width:1200px;text-align:center;font-family:"Montserrat",sans-serif;font-size:35px;line-height:49px;color:var(--white);font-weight:600}
.hero-title .greet{color:var(--teal-light);display:block;font-weight:500}
.intro-head{top:800px;left:60px;width:1080px;text-align:center;font-family:"Montserrat",sans-serif;font-weight:600;font-size:25px;line-height:39px;color:var(--teal-dark)}
.copy{font-size:16.5px;line-height:31.5px;color:var(--ink);width:515px}
.copy p+p{margin-top:15px}
.band-head{top:1610px;left:90px;width:1020px;text-align:center;font-family:"Montserrat",sans-serif;font-weight:600;font-size:26px;line-height:38px;color:var(--white)}
.point{left:76px;display:flex;width:610px}
.point-num{flex:none;width:75px;height:75px;border-radius:50%;background:var(--teal-light);color:var(--white);font-family:"Montserrat",sans-serif;font-weight:700;font-style:italic;font-size:40px;line-height:75px;text-align:center}
.point-text{margin-left:20px;font-size:16.5px;line-height:29px;color:var(--white)}
.cta{left:616px;top:2736px;width:267px;height:70px;border-radius:35px;background:var(--orange);color:var(--white);font-family:"Montserrat",sans-serif;font-weight:600;font-size:22px;line-height:70px;text-align:center;text-decoration:none}
.footer{left:0;top:2956px;width:1200px;height:243px;background:var(--footer)}
.footer-nav{position:absolute;top:63px;left:0;width:1200px;display:flex;justify-content:center;gap:49px}
.footer-nav a{font-family:"Montserrat",sans-serif;font-weight:600;font-size:16px;color:var(--white);text-decoration:none}
.copyright{position:absolute;top:103px;left:0;width:1200px;text-align:center;font-family:"Montserrat",sans-serif;font-size:15px;color:var(--white);letter-spacing:.4px}
.social{position:absolute;top:152px;left:502px;display:flex;gap:7px}
.social span{width:34px;height:34px;border-radius:50%;border:1.5px solid var(--white)}
</style>
</head>
<body>

<header>
  <div class="abs hero" role="img" aria-label="Black and white photo of parents cradling their newborn"></div>
  <div class="abs brand"><span class="brand-dot"></span><span class="brand-name">Harbor Nest</span></div>
  <nav class="abs nav">
    <a class="active" href="#" style="left:417px">HOME</a>
    <a href="#" style="left:546px">ABOUT</a>
    <a href="#" style="left:692px">SERVICES</a>
    <a href="#" style="left:830px">FAQS</a>
    <a href="#" style="left:948px">BLOG</a>
    <a href="#" style="left:1084px">CONTACT</a>
  </nav>
  <h1 class="abs hero-title"><span class="greet">Congratulations on your birth &amp;</span>WELCOME TO HARBOR NEST<br>POSTPARTUM CARE!</h1>
</header>

<main>
  <h2 class="abs intro-head">Hi, I'm Dana Reyes, a certified postpartum care expert and educator serving families of all varieties in the greater San Diego area and beyond.</h2>

  <svg class="abs" style="left:55px;top:897px" width="540" height="540" viewBox="0 0 540 540" role="img" aria-label="Photo of the doula holding a newborn in a pink outfit">
    <defs><linearGradient id="photoA" x1="0" y1="0" x2="1" y2="1"><stop offset="0" stop-color="#8a5a48"/><stop offset=".5" stop-color="#c9a08e"/><stop offset="1" stop-color="#3a2a30"/></linearGradient></defs>
    <circle cx="270" cy="270" r="262" fill="var(--teal-light)"/>
    <circle cx="262" cy="262" r="253" fill="url(#photoA)"/>
    <circle cx="270" cy="262" r="228" fill="none" stroke="#fff" stroke-width="2"/>
  </svg>

  <div class="abs copy" style="left:616px;top:950px">
    <p>My passion as a professional is showing new parents just like you that whether you've just had your first child or your fifth, you cannot only survive your postpartum period (also known as the 4th trimester), but you and your family can THRIVE – with the kind of compassionate, skilled, and targeted support for your unique needs that only an expert can provide.<br>That's where I come in.</p>
    <p>Did you know that, on average, new parents won't see their midwife or obstetrician until 6 weeks after giving birth to their baby(ies)? Working with a postpartum care expert (also known as a doula) can help fill in this gap in continuity of care by providing individualized support for parents and families as they transition to life with their new baby.</p>
  </div>

  <svg class="abs" style="left:0;top:1500px" width="1200" height="712" viewBox="0 0 1200 712">
    <path d="M0 0 Q600 92 1200 0 L1200 711 Q600 624 0 711 Z" fill="var(--teal-band)"/>
  </svg>

  <h2 class="abs band-head">My work includes four key areas of support that are designed to positively impact&nbsp; your postpartum period with your baby:</h2>

  <div class="abs point" style="top:1722px"><span class="point-num">1</span><p class="point-text">I enhance <b>bonding and attachment</b> between parents(s) and baby in the areas of feeding, soothing, learning baby's cues, babywearing, and playing with baby.</p></div>
  <div class="abs point" style="top:1824px"><span class="point-num">2</span><p class="point-text">I provide <b>practical, evidence-based information</b> about baby care and help identify what is normal and what is outside the range<br>of normal for parent(s) and baby.</p></div>
  <div class="abs point" style="top:1927px"><span class="point-num">3</span><p class="point-text">I prioritize the <b>mental and emotional health</b> of parent(s) and help identify potential warning signs that indicate that medical<br>care may be needed.</p></div>
  <div class="abs point" style="top:2030px"><span class="point-num">4</span><p class="point-text">I offer <b>hands-on support</b> with baby(ies), older siblings, pets, and light home upkeep and meal preparation.</p></div>

  <div class="abs" style="left:704px;top:1721px;width:421px;height:549px;border-radius:62px;background:linear-gradient(160deg,#6f7a80 0%,#c79a86 40%,#2e5a6e 75%,#2a4a5a 100%)" role="img" aria-label="Photo of the doula hugging newborn twins"></div>

  <svg class="abs" style="left:55px;top:2352px" width="540" height="540" viewBox="0 0 540 540" role="img" aria-label="Photo of the doula with new parents holding their swaddled baby">
    <defs><linearGradient id="photoB" x1="0" y1="0" x2="1" y2="1"><stop offset="0" stop-color="#b9a89a"/><stop offset=".5" stop-color="#5a4038"/><stop offset="1" stop-color="#d8d2cc"/></linearGradient></defs>
    <circle cx="270" cy="270" r="262" fill="var(--teal-light)"/>
    <circle cx="262" cy="262" r="253" fill="url(#photoB)"/>
    <circle cx="270" cy="262" r="228" fill="none" stroke="#fff" stroke-width="2"/>
  </svg>

  <div class="abs copy" style="left:616px;top:2418px">
    <p>Families who work with me report feeling more connected, happy, and informed than their parenting-veteran friends and family members – both during the time that I work with<br>them and beyond.</p>
    <p>Struggle is a normal part of growth and learning. Your postpartum period is a time for healing and recovering from birth, bonding with your baby, and establishing a healthy feeding relationship in whatever way works best for your family. Let me show you how to remove the struggle from this magical time!</p>
  </div>

  <a class="abs cta" href="#">Let's Get Started</a>
</main>

<footer class="abs footer">
  <nav class="footer-nav">
    <a href="#">HOME</a><a href="#">ABOUT</a><a href="#">SERVICES</a><a href="#">FAQS</a><a href="#">BLOG</a><a href="#">CONTACT</a>
  </nav>
  <p class="copyright">Copyright © 2021 Company Name All Rights Reserved</p>
  <div class="social"><span></span><span></span><span></span><span></span><span></span></div>
</footer>

</body>
</html>
```